Namibia currently imports 60% of its food. Harvest Crest Oruva is an initiative which will assist Namibia to become self sustainable in terms of food production. We aim to do this through the development of 3 agricultural production zones which will include farming zones, local farmer assistance, processing and distribution of the final products. Please see our project overview attached.

```html
<!DOCTYPE html>
<html lang="en">
<head>
<meta charset="utf-8">
<title>Harvest Crest Oruva – Food Security</title>
<link href="https://fonts.googleapis.com/css2?family=Merriweather:wght@300;400;700&display=swap" rel="stylesheet">
<style>
:root{
  --green:#0e6b3c;
  --tan:#c4a07a;
  --ink:#2b2b2b;
  --muted:#444;
  --card-border:#d3e6df;
  --white:#ffffff;
}
*{box-sizing:border-box;margin:0;padding:0}
html,body{width:1200px;height:3493px;overflow:hidden;background:var(--white)}
body{position:relative;font-family:'Merriweather',Georgia,serif;color:var(--ink)}
.abs{position:absolute}

/* header */
.brand{left:111px;top:52px;width:320px;text-align:center}
.brand-name{font-size:30px;color:var(--green);font-weight:400;letter-spacing:1px;white-space:nowrap}
.brand-rule{height:2px;background:var(--tan);margin-top:8px}
.contact{display:flex;align-items:center;gap:18px}
.contact .dot{width:50px;height:50px;border-radius:50%;background:var(--green);display:flex;align-items:center;justify-content:center;flex:none}
.contact .label{font-size:15px;color:var(--green);font-weight:700}
.contact .value{font-size:18px;color:#444;margin-top:6px;white-space:nowrap}
.nav{top:112px;left:492px;display:flex;gap:27px;font-size:13.5px;color:#333;white-space:nowrap}
.nav .active{color:var(--tan)}

/* hero */
.hero{left:0;top:140px;width:1200px;height:520px;background:linear-gradient(180deg,#cfe6de 0%,#8fa889 30%,#6c7d52 60%,#4d6a2f 100%)}
.hero-welcome{left:108px;top:308px;color:#fff;font-size:28px;font-weight:700}
.hero-title{left:108px;top:355px;color:#fff;font-size:54px;font-weight:700}
.play{left:828px;top:355px;width:60px;height:60px;border-radius:50%;background:var(--green);display:flex;align-items:center;justify-content:center}

/* intro */
.section-title{left:0;width:1200px;text-align:center;color:var(--green);font-size:46px;font-weight:700}
.title-rule{left:550px;width:100px;height:2px;background:var(--tan)}
.lead{left:155px;width:890px;text-align:center;font-size:21px;line-height:30px;color:#222}
.lead .hl{color:var(--tan)}

.zone{width:304px;height:285px;border:3px solid var(--card-border);border-radius:14px;background:#fff;text-align:center;padding-top:52px}
.zone svg{display:block;margin:0 auto 20px}
.zone h3{font-size:29px;color:var(--green);font-weight:700;line-height:38px}
.zone p{font-size:29px;color:var(--tan);font-weight:700;line-height:38px}

.photo{border-radius:2px}
.sub-title{color:var(--tan);font-size:32px;font-weight:700;line-height:44px}
.body-text{font-size:15.5px;line-height:26px;color:#333}

/* services */
.fields{left:0;top:2560px;width:1200px;height:515px;background:linear-gradient(180deg,#ffffff 0%,#e9efcf 18%,#b7c95f 40%,#7da238 70%,#5d8a2a 100%)}
.service{width:227px;height:263px;border:3px solid var(--card-border);border-radius:14px;background:#fff;display:flex;align-items:center;justify-content:center;text-align:center;padding:0 40px;font-size:22px;line-height:33px;color:var(--green)}

/* footer */
.footer-name{left:111px;top:3232px;width:320px;font-size:30px;color:var(--green);font-weight:700;line-height:42px}
.foot-col h4{font-size:22px;color:var(--green);font-weight:700;margin-bottom:22px}
.foot-col li{list-style:none;font-size:16px;color:#333;line-height:39px}
.copy{top:3450px;left:111px;width:978px;display:flex;align-items:center;gap:28px;font-size:15px;color:#333}
.copy .line{flex:1;height:1px;background:#555}
</style>
</head>
<body>

<header>
  <div class="abs brand">
    <div class="brand-name">HARVEST CREST ORUVA</div>
    <div class="brand-rule"></div>
  </div>
  <div class="abs contact" style="left:585px;top:27px">
    <div class="dot"><svg width="22" height="22" viewBox="0 0 24 24"><path fill="#fff" d="M6.6 10.8a15.1 15.1 0 0 0 6.6 6.6l2.2-2.2c.3-.3.7-.4 1-.2 1.1.4 2.3.6 3.6.6.6 0 1 .4 1 1V20c0 .6-.4 1-1 1A17 17 0 0 1 3 4c0-.6.4-1 1-1h3.5c.6 0 1 .4 1 1 0 1.3.2 2.5.6 3.6.1.3 0 .7-.2 1z"/></svg></div>
    <div><div class="label">Call Us</div><div class="value">+ 1 555 010 2468</div></div>
  </div>
  <div class="abs contact" style="left:885px;top:27px">
    <div class="dot"><svg width="22" height="22" viewBox="0 0 24 24"><path fill="#fff" d="M3 5h18v14H3z"/><path fill="none" stroke="#0e6b3c" stroke-width="2" d="M3 6l9 7 9-7"/></svg></div>
    <div><div class="label">Email</div><div class="value">info@hco.example</div></div>
  </div>
  <nav class="abs nav">
    <span>Home</span><span class="active">Food Security</span><span>Farmer Empowerment &amp; Education</span><span>Sustainability</span><span>Contact Us</span>
  </nav>
</header>

<section>
  <div class="abs hero" role="img" aria-label="Smiling farmer holding a crate of fresh vegetables in a green crop field"></div>
  <div class="abs hero-welcome">Welcome To</div>
  <div class="abs hero-title">Food Security</div>
  <div class="abs play"><svg width="22" height="24" viewBox="0 0 22 24"><path fill="#fff" d="M3 2l17 10L3 22z"/></svg></div>
</section>

<section>
  <h2 class="abs section-title" style="top:735px">Food Security</h2>
  <div class="abs title-rule" style="top:810px"></div>
  <p class="abs lead" style="top:845px">The long term intention of the <span class="hl">Harvest Crest Oruva</span> program would be to establish 3 distinct food production and processing zones which have access to large amounts of arable land, with high quality soil and strong water resources, as well as good transport connections to relevant markets. They are:</p>

  <div class="abs zone" style="left:111px;top:1015px">
    <svg width="80" height="80" viewBox="0 0 80 80"><circle cx="40" cy="40" r="36" fill="none" stroke="#0e6b3c" stroke-width="3"/><path d="M40 62V20M40 30c-8-2-10-8-8-12 6 2 8 6 8 12zm0 0c8-2 10-8 8-12-6 2-8 6-8 12zm0 12c-9-2-12-8-10-13 7 2 10 7 10 13zm0 0c9-2 12-8 10-13-7 2-10 7-10 13z" fill="none" stroke="#0e6b3c" stroke-width="3"/></svg>
    <h3>Otavi Region</h3><p>Central Namibia</p>
  </div>
  <div class="abs zone" style="left:448px;top:1015px">
    <svg width="80" height="80" viewBox="0 0 80 80"><circle cx="40" cy="40" r="34" fill="none" stroke="#0e6b3c" stroke-width="3" stroke-dasharray="150 10"/><path d="M40 22l10 28-10-6-10 6z" fill="#0e6b3c"/><text x="40" y="78" font-size="14" text-anchor="middle" fill="#0e6b3c" font-family="Merriweather,serif">N</text></svg>
    <h3>Kavango Region</h3><p>North Namibia</p>
  </div>
  <div class="abs zone" style="left:785px;top:1015px">
    <svg width="96" height="90" viewBox="0 0 96 90"><circle cx="48" cy="44" r="30" fill="none" stroke="#0e6b3c" stroke-width="3"/><path d="M48 4v16M48 68v6M8 44h16M72 44h16M36 36h24L48 58z" fill="none" stroke="#0e6b3c" stroke-width="3"/><text x="48" y="88" font-size="14" text-anchor="middle" fill="#0e6b3c" font-family="Merriweather,serif">S</text></svg>
    <h3>Neckartal Dam</h3><p>South Namibia</p>
  </div>

  <p class="abs lead" style="top:1343px;left:150px;width:900px">The Harvest Crest Oruva program is currently in the process of securing initial sites in Otavi and Kavango.The program aims to increase food production in Namibia through five distinctive mechanisms in each of the production zones. Our belief is that these key mechanisms need be initiatedsimultaneously in order to make a true difference to feed security in a Namibian context.</p>
</section>

<section>
  <div class="abs photo" style="left:111px;top:1570px;width:489px;height:295px;background:linear-gradient(135deg,#c9b9a7 0%,#b08a5c 50%,#8a6a3c 100%)" role="img" aria-label="Farmer in a straw hat holding fresh greens in a field"></div>
  <h3 class="abs sub-title" style="left:677px;top:1598px">Primary Production area</h3>
  <p class="abs body-text" style="left:677px;top:1662px;width:415px">Primary production will take place on parcels of land secured by Harvest Crest Oruva in the range of 600ha to 3,000ha. One quarter of developed land on each site will be utilised for the production of potatoes. The remainder will be used for staple food production,including maize and wheat.</p>

  <h3 class="abs sub-title" style="left:113px;top:1913px;width:430px">Empowerment Production area</h3>
  <p class="abs body-text" style="left:113px;top:2024px;width:420px">Namibia has a substantial amount of unutilised arable land in possession of either the government, or private individuals who do not have the resources or skills to develop the land into a viable food production asset. Harvest Crest Oruva aims to empower these organisations and individuals by assisting them to develop the land and operate them successfully. Support will come in the form of:</p>
  <div class="abs photo" style="left:600px;top:1922px;width:489px;height:294px;background:linear-gradient(180deg,#dfe3e6 0%,#b7ab93 40%,#9a7a58 100%)" role="img" aria-label="Workers harvesting potatoes into buckets in a field"></div>
</section>

<section>
  <div class="abs fields" role="img" aria-label="Sunlit green crop field"></div>
  <div class="abs service" style="left:111px;top:2290px">Provision of pivots and mobile drip irrigation on a lease to own basis</div>
  <div class="abs service" style="left:360px;top:2290px">Rental of tractors and impliments required</div>
  <div class="abs service" style="left:610px;top:2290px">Chemical and fertiliser supply</div>
  <div class="abs service" style="left:859px;top:2290px">Planting and harvesting services</div>
  <div class="abs service" style="left:237px;top:2582px">Full agronomy services and insurance</div>
  <div class="abs service" style="left:486px;top:2582px">Guaranteed purchase of all crops at market prices</div>
  <div class="abs service" style="left:735px;top:2582px">Costs to be paid for against product</div>
</section>

<footer>
  <div class="abs footer-name">Harvest Crest Oruva</div>
  <div class="abs foot-col" style="left:538px;top:3160px">
    <h4>Quick Links</h4>
    <ul><li>Home</li><li>Food Security</li><li>Farmer Empowerment and Education</li><li>Sustainability</li><li>Contact Us</li></ul>
  </div>
  <div class="abs foot-col" style="left:919px;top:3162px">
    <h4>Other Links</h4>
    <ul><li>Terms and conditions</li><li>Privacy policy</li><li>Career</li><li>Help center</li><li>Support</li></ul>
  </div>
  <div class="abs copy"><span class="line"></span><span>Copyright © 2024 Harvest Crest Oruva. All rights reserved.</span><span class="line"></span></div>
</footer>

</body>
</html>
```